Verodex business card

Business card for sustainable investment company called "Verodex". Verodex is an exchange platform selling carbon credits between buyers and sellers. Carbon Credits are an environmental commodity for reducing global carbon emissions.

the card should obviously have our logo and the theme should be sustainability/environment mixed with a trading platform.

Contact Information for Business Card

Logo, Name, Title, Phone, Email

Colors
0054AA
0677BA
7BADD7
CADEEF
E8F1F8
0094D4
00A9DD
6FCCEA
C7EBF8
E9F6FB
00AB8E
00BBA5
67D7C9
C6EFE9
E9F9F6
59FF00
82FF00
B8FF75
E3FFCB
F4FFEA

```html
<!DOCTYPE html>
<html lang="en">
<head>
<meta charset="utf-8">
<title>Verodex business card</title>
<link rel="stylesheet" href="https://fonts.googleapis.com/css2?family=Open+Sans:wght@400;600;700&display=swap">
<style>
  :root {
    --page-bg: #e6e8eb;
    --card-bg: #1e1f24;
    --card-edge: #2a2b31;
    --deco-dark: #16171b;
    --deco-light: #2c2d33;
    --brand-blue: #0094d4;
    --name-blue: #3e9fd6;
    --accent-light: #6fccea;
    --text-light: #f2f4f6;
    --text-muted: #cfd3d8;
  }
  * { box-sizing: border-box; margin: 0; padding: 0; }
  html, body { width: 1200px; height: 780px; overflow: hidden; }
  body {
    background: var(--page-bg);
    font-family: "Open Sans", sans-serif;
    position: relative;
  }
  .card {
    position: absolute;
    top: 225px;
    width: 540px;
    height: 330px;
    background: var(--card-bg);
    border-radius: 22px;
    overflow: hidden;
    box-shadow: 0 14px 30px rgba(0,0,0,0.25);
  }
  .card--front { left: 40px; }
  .card--back { left: 620px; }

  /* front */
  .brand {
    position: absolute;
    left: 32px; top: 30px;
    display: flex; align-items: center; gap: 12px;
  }
  .brand__mark {
    width: 22px; height: 22px;
    background: var(--brand-blue);
  }
  .brand__name {
    font-weight: 700;
    font-size: 30px;
    letter-spacing: 1px;
    text-transform: uppercase;
    color: var(--text-light);
  }
  .contact {
    position: absolute;
    left: 32px; top: 120px;
    color: var(--text-light);
    font-size: 14px;
    line-height: 1.45;
  }
  .contact__address { margin-bottom: 6px; }
  .contact__row { display: flex; align-items: center; gap: 8px; }
  .contact__row svg { width: 12px; height: 12px; fill: var(--text-muted); flex: none; }
  .person {
    position: absolute;
    right: 34px; top: 118px;
    text-align: right;
  }
  .person__name {
    font-weight: 600;
    font-size: 30px;
    color: var(--name-blue);
    letter-spacing: 0.5px;
  }
  .person__title {
    font-size: 16px;
    color: var(--text-light);
    margin-top: 2px;
  }
  .accent-bar {
    position: absolute;
    right: 0; top: 128px;
    width: 12px; height: 48px;
    background: linear-gradient(180deg, var(--accent-light), var(--brand-blue));
  }
  .front-decoration {
    position: absolute;
    left: 250px; top: 195px;
    width: 230px; height: 135px;
    border-radius: 14px 14px 0 0;
    background: linear-gradient(135deg, var(--deco-light), var(--deco-dark));
  }

  /* back */
  .back-pattern {
    position: absolute; inset: 0;
    background: linear-gradient(160deg, #232429, #1a1b1f);
  }
  .back-brand {
    position: absolute;
    left: 50%; top: 50%;
    transform: translate(-50%, -50%);
    display: flex; align-items: center; gap: 10px;
    background: var(--card-bg);
    padding: 10px 16px;
    border-radius: 8px;
  }
  .back-brand__mark { width: 16px; height: 16px; background: var(--brand-blue); }
  .back-brand__name {
    font-weight: 700;
    font-size: 22px;
    color: var(--brand-blue);
    text-transform: uppercase;
    letter-spacing: 1px;
  }
</style>
</head>
<body>
  <section class="card card--front" aria-label="Card front">
    <div class="brand">
      <span class="brand__mark"></span>
      <span class="brand__name">Verodex</span>
    </div>

    <div class="contact">
      <p class="contact__address">1840 Harbor Ridge Rd. Suite 300<br>Dallin, TX 75014</p>
      <p class="contact__row">
        <svg viewBox="0 0 24 24" aria-hidden="true"><path d="M6.6 10.8a15.1 15.1 0 0 0 6.6 6.6l2.2-2.2a1 1 0 0 1 1-.25 11.4 11.4 0 0 0 3.6.57 1 1 0 0 1 1 1V20a1 1 0 0 1-1 1A17 17 0 0 1 3 4a1 1 0 0 1 1-1h3.5a1 1 0 0 1 1 1c0 1.25.2 2.45.57 3.57a1 1 0 0 1-.25 1z"/></svg>
        (555) 214-3086
      </p>
      <p class="contact__row">
        <svg viewBox="0 0 24 24" aria-hidden="true"><path d="M2 5h20v14H2zm2 2v.5l8 5 8-5V7l-8 5z"/></svg>
        hello@verodex.com
      </p>
      <p class="contact__row">
        <svg viewBox="0 0 24 24" aria-hidden="true"><circle cx="12" cy="12" r="10"/></svg>
        www.verodex.com
      </p>
    </div>

    <div class="person">
      <p class="person__name">Lena Marvik</p>
      <p class="person__title">Managing Director</p>
    </div>
    <span class="accent-bar"></span>

    <div class="front-decoration" role="img" aria-label="Large embossed brand emblem decoration"></div>
  </section>

  <section class="card card--back" aria-label="Card back">
    <div class="back-pattern" role="img" aria-label="Repeating embossed brand emblem pattern"></div>
    <div class="back-brand">
      <span class="back-brand__mark"></span>
      <span class="back-brand__name">Verodex</span>
    </div>
  </section>
</body>
</html>
```